Hollow Thicket, a 3d voxel survival video game needs a card for gaming conventions

I am the lead developer for Hollow Thicket http://www.HollowThicket.example and need a business card to hand out at an indie gaming convention
The card would need to include the game name, website url, my name, position (Lead Developer), e-mail and phone number
The game is a 3d, voxel (with smooth terrain) based survival game with guns and wildlife. The main icon of the game would likely be a grizzly bear but I am willing to accept other designs too.
Attached is a media kit for the game with some images you can use but don't have to its just what little art I can provide. Anything on the website or from the video game can also be used. unrelated art can also be used.
Target Market(s)
Indie Developers/publishers at conferences
Industry/Entity Type
Games
Contact Information for Business Card
Name: Corin Waldrick
Position: Lead Developer
E-mail: Pale_Kettle@mailbox.example
Phone number: 555-372-1186

```html
<!DOCTYPE html>
<html lang="en">
<head>
<meta charset="utf-8">
<title>Hollow Thicket – Business Card</title>
<link rel="stylesheet" href="https://fonts.googleapis.com/css2?family=Open+Sans:wght@400;600&family=Russo+One&display=swap">
<style>
  :root {
    --backdrop: #e9e9e9;
    --card-white: #ffffff;
    --olive-dark: #23230c;
    --olive-mid: #5e5a36;
    --sand-light: #ddd3b4;
    --edge-orange: #e8731c;
    --brand-red: #9e1c12;
    --brand-gold: #a98a52;
    --ink: #3a3a3a;
    --ink-soft: #555555;
    --bear-brown: #6e4a2e;
    --bear-light: #9a6e48;
  }
  * { box-sizing: border-box; margin: 0; padding: 0; }
  html, body {
    width: 1200px;
    height: 900px;
    overflow: hidden;
    background: var(--backdrop);
  }
  .stage {
    position: relative;
    width: 1200px;
    height: 900px;
    display: flex;
    align-items: center;
    justify-content: center;
    gap: 60px;
  }
  .card {
    position: relative;
    width: 525px;
    height: 300px;
    overflow: hidden;
    box-shadow: 0 6px 18px rgba(0,0,0,0.12);
  }

  /* Back side: contact details */
  .card-back {
    background: var(--card-white);
    font-family: "Open Sans", sans-serif;
  }
  .card-back .game-name {
    position: absolute;
    top: 58px;
    left: 0;
    right: 0;
    text-align: center;
    font-family: "Russo One", sans-serif;
    font-size: 38px;
    letter-spacing: 2px;
    color: var(--brand-red);
  }
  .card-back .contact {
    position: absolute;
    top: 140px;
    left: 0;
    right: 0;
    text-align: center;
  }
  .person-name {
    font-size: 17px;
    font-weight: 600;
    letter-spacing: 0.5px;
  }
  .person-name .first { color: var(--brand-red); }
  .person-name .last { color: var(--brand-gold); }
  .person-role {
    font-size: 12px;
    color: var(--ink-soft);
    margin-top: 2px;
  }
  .contact-lines {
    list-style: none;
    margin-top: 12px;
    font-size: 13px;
    color: var(--ink);
  }
  .contact-lines li {
    display: flex;
    align-items: center;
    justify-content: center;
    gap: 6px;
    line-height: 1.6;
  }
  .contact-lines svg { width: 11px; height: 11px; fill: var(--brand-red); }

  /* Front side: game face */
  .card-front {
    background: radial-gradient(ellipse 60% 70% at 50% 52%, var(--sand-light) 0%, var(--olive-mid) 55%, var(--olive-dark) 100%);
    border-top: 3px solid var(--edge-orange);
  }
  .card-front .key-art {
    position: absolute;
    left: 20px;
    top: 44px;
    width: 260px;
    height: 140px;
    border-radius: 40% 50% 30% 30%;
    background: radial-gradient(ellipse at 60% 40%, var(--bear-light), var(--bear-brown) 70%, rgba(110,74,46,0) 100%);
  }
  .card-front .game-name {
    position: absolute;
    right: 28px;
    bottom: 46px;
    font-family: "Russo One", sans-serif;
    font-size: 34px;
    letter-spacing: 2px;
    color: var(--brand-red);
  }
</style>
</head>
<body>
<main class="stage">
  <section class="card card-back" aria-label="Card back with contact details">
    <h1 class="game-name">HOLLOW THICKET</h1>
    <div class="contact">
      <p class="person-name"><span class="first">CORIN</span> <span class="last">WALDRICK</span></p>
      <p class="person-role">Lead Developer</p>
      <ul class="contact-lines">
        <li>
          <svg viewBox="0 0 24 24" aria-hidden="true"><path d="M6.6 10.8a15.1 15.1 0 0 0 6.6 6.6l2.2-2.2a1 1 0 0 1 1-.25 11.4 11.4 0 0 0 3.6.57 1 1 0 0 1 1 1V20a1 1 0 0 1-1 1A17 17 0 0 1 3 4a1 1 0 0 1 1-1h3.5a1 1 0 0 1 1 1c0 1.25.2 2.45.57 3.6a1 1 0 0 1-.25 1z"/></svg>
          555-372-1186
        </li>
        <li>
          <svg viewBox="0 0 24 24" aria-hidden="true"><path d="M2 5h20v14H2z M2 5l10 8 10-8" /></svg>
          Pale_Kettle@mailbox.example
        </li>
      </ul>
    </div>
  </section>

  <section class="card card-front" aria-label="Card front with game name">
    <div class="key-art" role="img" aria-label="Photograph of a brown grizzly bear walking"></div>
    <p class="game-name">HOLLOW THICKET</p>
  </section>
</main>
</body>
</html>
```